Tampa Bay fishing guide needs stunning website.

I currently have a site - www.reelcoveguide.net which I personally put together using the Pagely platform and I am looking for a redesign on a different platform (Sitecraft?) that will allow me to easily create landing pages in the future. Would like to have a block for visitors to opt in to newsletter. Need social media links on all pages.

I would like to let my visitors know that I am able to handle their fishing charter needs here in the Tampa Bay area, if I'm not available for the dates they are looking to go I can refer them to a reputable captain in the area.

Target Market(s)

United States

Industry/Entity Type

Tourism

Coding

Coded - Design and coding required

Number of Pages Required

5+ page

Font styles to use
Sans Serif

Colors
0355a3
3176b5
85abd2
fbf289

Requirements
Must have
• Mobile Responsive, Ability to insert Vantor Metrics, Chatterbox pixels, ability to add custom landing pages in future
Nice to have
• Clean, easy navigation

```html
<!DOCTYPE html>
<html lang="en">
<head>
<meta charset="utf-8">
<title>Capt. Wade Harlan – Tampa Bay Fishing Charters</title>
<link rel="stylesheet" href="https://fonts.googleapis.com/css2?family=Oswald:wght@400;500;600&family=Open+Sans:wght@400;600;700&display=swap">
<style>
:root{
  --navy:#0355a3;
  --blue:#3176b5;
  --sky:#85abd2;
  --yellow:#fbf289;
  --ink:#333;
  --light:#f3f3f3;
  --footer:#343434;
  --white:#fff;
}
*{box-sizing:border-box;margin:0;padding:0}
html,body{width:1200px;height:2616px;overflow:hidden}
body{position:relative;font-family:"Open Sans",Arial,sans-serif;color:var(--ink);background:var(--white)}
.abs{position:absolute}
.heading{font-family:"Oswald",Arial,sans-serif;font-weight:500;text-transform:uppercase}

/* header */
.hero{left:0;top:0;width:1200px;height:596px;background:linear-gradient(180deg,#cfe0ee 0%,#a9c9dc 18%,#5fa6b4 40%,#3f8e9d 70%,#2f7886 100%)}
.hero-boat{left:0;top:320px;width:380px;height:220px;background:linear-gradient(180deg,#8a8f95,#e9ecef);border-radius:0 0 40px 0}
.hero-fish{left:760px;top:180px;width:180px;height:230px;background:linear-gradient(160deg,#8fa2ad,#c4cfd5);border-radius:50%;opacity:.6}
.navbar{left:0;top:61px;width:1200px;height:35px;background:var(--navy)}
.nav{left:466px;top:61px;height:35px;display:flex;list-style:none;font-size:11px;font-weight:600;color:var(--white);text-transform:uppercase}
.nav li{position:absolute;top:0;height:35px;line-height:35px;white-space:nowrap}
.nav .active{background:var(--yellow);color:var(--navy);padding:0 14px}
.brand{left:131px;top:24px;width:239px;height:98px;background:var(--white);display:flex;align-items:center;justify-content:center;gap:10px}
.brand-mark{width:16px;height:16px;background:var(--blue)}
.brand-name{font-family:"Oswald",Arial,sans-serif;font-weight:600;font-size:24px;color:var(--blue)}
.call{left:810px;top:18px;display:flex;align-items:center;gap:10px;font-size:12px;color:#223}
.call strong{font-size:18px;color:var(--navy);font-weight:700}
.call-icon{width:28px;height:28px;border:2px solid var(--navy);border-radius:50%;display:flex;align-items:center;justify-content:center}
.hero-title{left:392px;top:290px;width:330px;font-size:27px;line-height:38px;color:var(--white);font-weight:600}
.dots{left:538px;top:550px;display:flex;gap:17px}
.dots span{width:10px;height:10px;border-radius:50%;background:var(--white)}
.dots span.on{background:transparent;border:2px solid var(--white)}

/* features */
.features{left:0;top:596px;width:1200px;height:161px;background:var(--navy)}
.feature{top:27px;display:flex;gap:16px;color:var(--white)}
.feature-icon{width:108px;height:108px;border-radius:50%;background:var(--yellow);display:flex;align-items:center;justify-content:center;flex:none}
.feature h3{font-size:17px;margin-top:15px;font-weight:500}
.feature p{font-size:11px;line-height:16px;width:170px;margin-top:6px}

/* intro */
.intro{left:0;top:757px;width:1200px;height:385px;background:var(--light)}
.crumb{left:131px;top:48px;font-size:11px}
.intro-title{left:131px;top:68px;width:420px;font-size:23px;line-height:36px;color:var(--navy);font-weight:600}
.intro-copy{left:131px;top:155px;width:475px;font-size:11.5px;line-height:18px}
.intro-copy p{margin-bottom:16px}
.intro-photo{left:644px;top:45px;width:423px;height:288px;background:linear-gradient(135deg,#2d4a2a,#6d8a5c 45%,#d8dcd8 75%,#b9c3c8);box-shadow:0 4px 10px rgba(0,0,0,.35)}

/* pickup */
.section-title{font-size:24px;font-weight:600}
.pickup-title{left:131px;top:1178px;color:var(--navy)}
.location{top:1231px;width:300px;height:241px;display:flex;flex-direction:column;align-items:center;justify-content:center;color:var(--white);text-align:center}
.location h3{font-size:21px;font-weight:600;letter-spacing:.5px}
.location p{font-size:12px;margin-top:2px}

/* rates */
.rates{left:0;top:1514px;width:1200px;height:418px;background:var(--blue);color:var(--white)}
.rates-title{left:131px;top:26px}
.rate{top:82px;width:300px}
.rate-photo{width:300px;height:240px;position:relative}
.price{position:absolute;left:0;width:70px;height:52px;background:var(--yellow);color:var(--navy);padding:5px 0 0 8px}
.price small{display:block;font-size:11px}
.price b{font-size:20px;font-weight:700}
.rate h3{font-size:16px;margin-top:22px;font-weight:500}
.rate p{font-size:10.5px;margin-top:2px}

/* testimonials */
.testimonials{left:0;top:1932px;width:1200px;height:288px;background:var(--sky);color:var(--white)}
.testimonials-title{left:131px;top:32px}
.quote{top:86px;width:296px;height:157px;border:2px solid #d3e1ef;text-align:center;padding:24px 28px 0}
.quote .mark{position:absolute;left:26px;top:14px;font-family:Georgia,serif;font-size:52px;line-height:52px}
.quote p{font-size:14px;line-height:22px}
.quote hr{width:40px;border:0;border-top:1px solid var(--white);margin:12px auto 8px}
.quote cite{font-style:normal;font-size:10px;font-weight:700}

/* footer */
.footer{left:0;top:2220px;width:1200px;height:396px;background:var(--footer);color:var(--white)}
.footer-brand{left:131px;top:62px;display:flex;align-items:center;gap:12px}
.footer-brand .brand-name{font-size:28px}
.footer h4{font-family:"Oswald",Arial,sans-serif;font-weight:500;font-size:13px;text-transform:uppercase}
.contact{left:424px;top:48px;font-size:11px;line-height:24px}
.contact h4{margin-bottom:10px}
.menu{left:659px;top:48px;font-size:11px;line-height:28px;list-style:none}
.menu h4{margin-bottom:4px}
.badge{top:42px;width:127px;height:101px;background:var(--white)}
.card{top:173px;width:48px;height:30px;background:#e9e9e9;border-radius:3px}
.follow{left:828px;top:246px;display:flex;align-items:center;gap:9px}
.follow span{font-family:"Oswald",Arial,sans-serif;font-size:12px;margin-right:4px}
.follow i{width:25px;height:25px;border-radius:50%;background:var(--blue)}
.newsletter-title{left:131px;top:186px;font-size:16px}
.field{top:216px;height:48px;border:1px solid #777;display:flex;align-items:center;gap:12px;padding-left:20px;font-size:12px}
.signup{left:518px;top:216px;width:93px;height:48px;background:var(--yellow);color:var(--ink);font-family:"Oswald",Arial,sans-serif;font-size:17px;display:flex;align-items:center;justify-content:center}
.rule{left:131px;top:318px;width:936px;border-top:1px solid #666}
.copyright{left:0;top:350px;width:1200px;text-align:center;font-size:10px}
</style>
</head>
<body>

<header>
  <div class="abs hero" role="img" aria-label="Angler on a boat fighting a tarpon leaping from the water of Tampa Bay"></div>
  <div class="abs navbar"></div>
  <ul class="abs nav">
    <li class="active" style="left:0">Home</li>
    <li style="left:94px">About us</li>
    <li style="left:197px">Pick up locations</li>
    <li style="left:355px">Rates</li>
    <li style="left:436px">Contact us</li>
    <li style="left:547px">Gift card</li>
  </ul>
  <div class="abs brand"><span class="brand-mark"></span><span class="brand-name">Capt. Wade Harlan</span></div>
  <div class="abs call">
    <span class="call-icon"><svg width="14" height="14" viewBox="0 0 24 24"><path fill="#0355a3" d="M6.6 10.8a15 15 0 0 0 6.6 6.6l2.2-2.2c.3-.3.7-.4 1-.2 1.1.4 2.3.6 3.6.6.6 0 1 .4 1 1V20c0 .6-.4 1-1 1A17 17 0 0 1 3 4c0-.6.4-1 1-1h3.5c.6 0 1 .4 1 1 0 1.3.2 2.5.6 3.6.1.3 0 .7-.2 1z"/></svg></span>
    <span>Call Capt. Wade</span><strong>(813) 555-0147</strong>
  </div>
  <h1 class="abs heading hero-title">Come fish with Tampa Bay, FL fishing guide, Tampa Bay fishing charter most respected captain, 25 year native guide.</h1>
  <div class="abs dots"><span></span><span class="on"></span><span></span><span></span><span></span></div>
</header>

<section class="abs features">
  <div class="abs feature" style="left:131px">
    <div class="feature-icon"><svg width="54" height="54" viewBox="0 0 48 48" fill="none" stroke="#0355a3" stroke-width="2.5"><circle cx="22" cy="26" r="15"/><path d="M7 26h30M22 11c-6 8-6 22 0 30M22 11c6 8 6 22 0 30"/><circle cx="36" cy="10" r="5" fill="#0355a3"/></svg></div>
    <div><h3 class="heading">Book a spot</h3><p>Lorem Ipsum is simply dummy text of the printing and typeset Lorem Ipsum.</p></div>
  </div>
  <div class="abs feature" style="left:460px">
    <div class="feature-icon"><svg width="54" height="54" viewBox="0 0 48 48" fill="none" stroke="#0355a3" stroke-width="2.5"><circle cx="18" cy="14" r="8"/><circle cx="32" cy="20" r="7"/><path d="M4 40h8l10-6h12l8-6M12 34v8"/></svg></div>
    <div><h3 class="heading">Lower price</h3><p>Lorem Ipsum is simply dummy text of the printing and typeset Lorem Ipsum.</p></div>
  </div>
  <div class="abs feature" style="left:783px">
    <div class="feature-icon"><svg width="54" height="54" viewBox="0 0 48 48" fill="none" stroke="#0355a3" stroke-width="2.5"><rect x="6" y="9" width="36" height="32" rx="3"/><path d="M6 17h36M14 5v8M34 5v8M13 24h4M22 24h4M31 24h4M13 32h4M22 32h4"/></svg></div>
    <div><h3 class="heading">Available dates</h3><p>Lorem Ipsum is simply dummy text of the printing and typeset Lorem Ipsum.</p></div>
  </div>
</section>

<section class="abs intro">
  <p class="abs crumb">Tampa Bay Fishing Charters Florida | Fishing Charters Tampa Bay</p>
  <h2 class="abs heading intro-title">Tampabay, fishingguide, tampabay fishingcharters</h2>
  <div class="abs intro-copy">
    <p>Capt. Wade Harlan, with over 20 years' experience, Native fishing charter tampa charter captain offering full and half day fishing charters on the waters of Tampa Bay.</p>
    <p>If you're looking for a great fishing charter tampa don't hesitate to contact Capt. Wade or you can simply book your trip online here.</p>
    <p>Come enjoy a wonderful day fishing charters Tampa for Tarpon, Snook, Redfish, Trout, Sharks, Cobia, Spanish mackerel as well as others aboard Capt. Wade Harlan Sport fishing Charters boat. Capt. Wade will work hard to ensure that you and your guests have a memorable day enjoying the wonderful gamefish that Tampa Bay has to offer</p>
  </div>
  <div class="abs intro-photo" role="img" aria-label="Anglers on a boat releasing a large tarpon"></div>
</section>

<section>
  <h2 class="abs heading section-title pickup-title">Pickup locations</h2>
  <div class="abs location" style="left:132px;background:linear-gradient(180deg,#8aa3b5,#3e5a6e)" role="img" aria-label="Aerial view of a waterfront city skyline"><h3 class="heading">Pelican Cove Marina</h3><p>St. Petersburg</p></div>
  <div class="abs location" style="left:450px;background:linear-gradient(180deg,#4a5b78,#1f2a44 60%,#5a4a3a)" role="img" aria-label="Tampa skyline at night reflected in the water"><h3 class="heading">Bayview Boat Ramp</h3><p>Tampa</p></div>
  <div class="abs location" style="left:766px;background:linear-gradient(160deg,#1d5a6c,#0b3444)" role="img" aria-label="Aerial view of a boat on dark blue water"><h3 class="heading">Silver Tide Boat Ramp</h3><p>Holmes Beach</p></div>
</section>

<section class="abs rates">
  <h2 class="abs heading section-title rates-title">Rates</h2>
  <div class="abs rate" style="left:132px">
    <div class="rate-photo" style="background:linear-gradient(180deg,#3f6b3a,#6f8f62 50%,#2f5aa8)" role="img" aria-label="Angler holding a snook">
      <div class="price" style="top:78px"><small>1-3 People</small><b>$399</b></div>
      <div class="price" style="top:152px"><small>4 People</small><b>$499</b></div>
    </div>
    <h3 class="heading">Half day (4 hour)</h3><p>Enjoy a half day trip on the beautiful waters of Tampa Bay</p>
  </div>
  <div class="abs rate" style="left:450px">
    <div class="rate-photo" style="background:linear-gradient(180deg,#9fb0b8,#6f8a96 50%,#3a6fa8)" role="img" aria-label="Two anglers holding a tarpon">
      <div class="price" style="top:78px"><small>1-3 People</small><b>$499</b></div>
      <div class="price" style="top:152px"><small>4 People</small><b>$599</b></div>
    </div>
    <h3 class="heading">3/4 day (6 hours)</h3><p>Our most popular and recommended trip</p>
  </div>
  <div class="abs rate" style="left:766px">
    <div class="rate-photo" style="background:linear-gradient(135deg,#2f7a5c,#1e5e48 55%,#e6ebee)" role="img" aria-label="Anglers on a boat handling a large fish">
      <div class="price" style="top:78px"><small>1-3 People</small><b>$599</b></div>
      <div class="price" style="top:152px"><small>4 People</small><b>$699</b></div>
    </div>
    <h3 class="heading">Full day (8 hours)</h3><p>Enjoy a full day trip on the beautiful waters of Tampa Bay.</p>
  </div>
</section>

<section class="abs testimonials">
  <h2 class="abs heading section-title testimonials-title">Testimonials</h2>
  <blockquote class="abs quote" style="left:131px"><span class="mark">“</span><p>Capt. Wade has always been a 100% er for me</p><hr><cite>Frank Dowling,</cite></blockquote>
  <blockquote class="abs quote" style="left:451px"><span class="mark">“</span><p>Truly a master angler</p><hr><cite>Jan Moreau,</cite></blockquote>
  <blockquote class="abs quote" style="left:770px"><span class="mark">“</span><p>Congratulations on winning the Gulf Coast Celebrity Grand Slam Tournament</p><cite>Charlie Vance</cite></blockquote>
</section>

<footer class="abs footer">
  <div class="abs footer-brand"><span class="brand-mark"></span><span class="brand-name">Capt. Wade Harlan</span></div>
  <div class="abs contact"><h4>Contact us</h4><p>TEL: 813-555-0147</p><p>E-MAIL: captwade@harlanmail.net</p></div>
  <ul class="abs menu"><li><h4>Menu</h4></li><li>Home</li><li>About us</li><li>Pick up locations</li><li>Rates</li><li>Contact us</li><li>Gift card</li></ul>
  <div class="abs badge" style="left:802px" role="img" aria-label="Partner listing badge"></div>
  <div class="abs badge" style="left:936px" role="img" aria-label="Review site badge"></div>
  <div class="abs card" style="left:825px"></div>
  <div class="abs card" style="left:879px"></div>
  <div class="abs card" style="left:933px"></div>
  <div class="abs card" style="left:987px"></div>
  <div class="abs follow"><span>FOLLOW US :</span><i></i><i></i><i></i><i></i></div>
  <h4 class="abs newsletter-title">Newsletter signup!</h4>
  <div class="abs field" style="left:131px;width:185px"><svg width="10" height="11" viewBox="0 0 10 11"><circle cx="5" cy="3" r="2.5" fill="#fff"/><path d="M0 11c0-3 2-5 5-5s5 2 5 5z" fill="#fff"/></svg>Name</div>
  <div class="abs field" style="left:328px;width:178px"><svg width="12" height="9" viewBox="0 0 12 9"><rect width="12" height="9" fill="#fff"/><path d="M0 0l6 5 6-5" stroke="#343434" fill="none"/></svg>E mail id</div>
  <div class="abs signup">SIGNUP!</div>
  <div class="abs rule"></div>
  <p class="abs copyright">Copyrights @ 2016 All Rights Reserved</p>
</footer>

</body>
</html>
```